PitchTally Webpages and Logo

See attached brief. Take the existing website www.pitchtally.co.uk and logo and transform these assets to:

Give people who arrive on the site for first time the confidence to sign-up easily and quickly
Allow regular returning users quick and easy placing of predictions and encourage them to share the PitchTally prediction on social networks and with their contacts
Convey the essence of a community working together to enjoyably come-up with smart predictions on sporting events
Work seamlessly and well across smartphones, tablets and desktop i.e. Should be Responsive Web Design
Updates

Target Market(s)

Users are sports fans with opinions
Primarily male and early twenties to mid-thirties
They are competitive - they want to beat their peers
Many are from outside the UK

Industry/Entity Type

Events

Logo Text

PitchTally

Coding

Coded - Design and coding required

Number of Pages Required

4 page

Font styles to use
Sans Serif

Requirements
Must have
• Responsive Web Design
• Mobile First
• HTML must work with dedicated bespoke application developed in ASP.NET using MS SQL underneath
• See Brief
Nice to have
• See brief
Should not have
• See brief

```html
<!DOCTYPE html>
<html lang="en">
<head>
<meta charset="utf-8">
<title>PitchTally</title>
<link href="https://fonts.googleapis.com/css2?family=Open+Sans:ital,wght@0,400;0,600;0,700;1,600&display=swap" rel="stylesheet">
<style>
:root{
  --blue:#2a8fc0;
  --blue-dark:#1d6f98;
  --black:#0b0b0b;
  --pink:#e0246e;
  --card:#f1f1f1;
  --footer:#4a4a4a;
  --text:#333;
  --muted:#888;
}
*{margin:0;padding:0;box-sizing:border-box}
html,body{width:779px;height:1200px;overflow:hidden}
body{font-family:'Open Sans',sans-serif;color:var(--text);background:#fff;position:relative}
.abs{position:absolute}
.topbar{left:0;top:0;width:779px;height:32px;background:#fff}
.kitty{left:39px;top:9px;font-size:10px;color:var(--blue)}
.kitty .up{color:#2e9a3a;font-weight:700;font-size:8px}
.btn-top{top:6px;height:20px;width:74px;background:var(--blue);color:#fff;font-size:10px;text-align:center;line-height:20px;border-radius:2px;box-shadow:inset 0 -2px 0 var(--blue-dark)}
.nav{left:0;top:32px;width:779px;height:55px;background:var(--black)}
.brand{left:39px;top:40px;display:flex;align-items:center;gap:8px;color:#fff;font-size:19px;font-weight:700}
.brand i{display:block;width:38px;height:38px;border-radius:50%;background:var(--blue)}
.menu{top:53px;font-size:10px;color:#fff;transform:translateX(-50%)}
.hero{left:0;top:87px;width:779px;height:347px;background:radial-gradient(ellipse at 50% 30%,#3d4a52 0%,#1f2a30 45%,#101619 100%)}
.hero-title{left:0;width:779px;text-align:center;color:#fff;font-size:24px}
.hero-title b{color:var(--pink);font-weight:700}
.hero-copy{left:100px;width:579px;top:188px;text-align:center;color:#fff;font-size:9.5px;line-height:14px;font-family:Georgia,serif}
.join{left:325px;top:232px;width:150px;height:39px;background:var(--blue);border:2px solid #4fb0de;color:#fff;font-weight:700;font-size:17px;text-align:center;line-height:35px;border-radius:2px}
.arrow{top:250px;color:#999;font-size:16px}
.tips{left:120px;top:291px;width:554px;height:102px;border:1px solid #ccc}
.tips-head{height:33px;background:#fff;display:flex;align-items:center;padding-left:57px;gap:40px}
.tips-head .t{font-style:italic;font-weight:600;color:var(--blue);font-size:14px}
.chip{font-size:7px;border:1px solid #ccc;padding:1px 3px;border-radius:2px;margin-right:3px;display:inline-block}
.chip.b{background:#3b5b98;color:#fff;border-color:#3b5b98}
.chip.t{background:#eaf3fa;color:#333}
.tips-body{height:68px;background:rgba(200,200,200,.75);display:flex}
.tips-col{flex:1;text-align:center;padding-top:7px;font-size:12px;color:#222}
.tips-col.mid{background:rgba(225,225,225,.8)}
.tips-col small{display:block;font-size:7.5px;color:#fff;margin-top:6px}
.tips-col.mid small{color:var(--blue);line-height:15px;margin-top:2px}
.features{left:39px;top:419px;width:701px;height:104px;background:#fff;box-shadow:0 2px 8px rgba(0,0,0,.25);display:flex}
.feat{flex:1;display:flex;padding:22px 0 0 21px;gap:10px;border-right:1px solid #e3e3e3}
.feat:last-child{border:0}
.feat .ic{width:52px;height:52px;background:var(--blue);border-radius:4px;flex:none;box-shadow:inset 0 -3px 0 var(--blue-dark)}
.feat h3{font-weight:400;font-size:15px;color:#222}
.feat p{font-size:7.5px;color:var(--muted);line-height:15px;width:140px}
.section-title{left:0;width:779px;top:544px;text-align:center;color:var(--blue);font-size:14px;font-weight:700}
.match{width:225px;height:178px;background:var(--card)}
.crest{position:absolute;top:26px;width:60px;height:60px;border-radius:50%;background:#fff}
.vs{position:absolute;left:0;width:225px;top:48px;text-align:center;font-size:13px;color:#222}
.team{position:absolute;top:94px;font-size:10px;color:var(--blue);width:112px;text-align:center}
.date{position:absolute;left:0;width:225px;top:117px;text-align:center;font-size:8px;color:#222}
.date i{display:inline-block;width:8px;height:8px;border:1.5px solid var(--blue);border-radius:50%;margin-right:8px;vertical-align:-1px}
.predict{position:absolute;left:0;bottom:0;width:225px;height:37px;background:var(--blue);color:#fff;font-weight:700;font-size:13.5px;text-align:center;line-height:37px}
.show-all{left:0;width:779px;top:993px;text-align:center;color:var(--blue);font-size:12px}
.footer{left:0;top:1027px;width:779px;height:173px;background:var(--footer)}
.fh{font-size:11.5px;color:var(--blue);top:1045px}
.flinks{font-size:7.5px;color:#ddd;line-height:10.8px;top:1066px}
.feedback{left:295px;top:1048px;width:187px;height:30px;border:1px solid var(--blue);color:var(--blue);font-size:11px;text-align:center;line-height:28px}
.social{top:1102px;width:24px;height:24px;background:#333;border-radius:3px}
.avatar{left:602px;top:1068px;width:49px;height:49px;border-radius:50%;background:linear-gradient(#cfd8de,#8fa3ae);border:2px solid #fff}
.quote{left:536px;top:1122px;width:200px;font-size:7.5px;color:#ddd;line-height:13px}
.by{left:650px;top:1146px;font-size:10px;color:#fff}
.copy{left:0;width:779px;top:1172px;text-align:center;font-size:6.5px;color:#ddd}
</style>
</head>
<body>
<div class="abs topbar"></div>
<div class="abs kitty">Kitty: £1289 <span class="up">▲5%</span></div>
<div class="abs btn-top" style="left:586px">Login</div>
<div class="abs btn-top" style="left:665px">Register</div>

<div class="abs nav"></div>
<div class="abs brand"><i></i>PitchTally</div>
<div class="abs menu" style="left:311px">Home</div>
<div class="abs menu" style="left:378px">About Us</div>
<div class="abs menu" style="left:448px">Tables</div>
<div class="abs menu" style="left:507px">Kitty</div>
<div class="abs menu" style="left:561px">FAQ</div>
<div class="abs menu" style="left:621px">History</div>
<div class="abs menu" style="left:689px">Contact</div>

<div class="abs hero" role="img" aria-label="Floodlit football stadium at night"></div>
<div class="abs hero-title" style="top:119px">Predict 6 scores</div>
<div class="abs hero-title" style="top:154px">to win <b>£250,000</b></div>
<div class="abs hero-copy">MAECENAS A SAPIEN TORTOR QUIS TINCIDUNT LECTUS. DONEC ULLAMCORPER DUI SIT AMET LOREM ULTRICES SED PORTTITOR MASSA EU DUI SCELERISQUE</div>
<div class="abs join">JOIN NOW</div>
<div class="abs arrow" style="left:40px">‹</div>
<div class="abs arrow" style="left:732px">›</div>

<div class="abs tips">
  <div class="tips-head">
    <span class="t">PitchTally Hot Tips!!</span>
    <span><span class="chip t">Follow @ScoreWatch</span><span class="chip">451K followers</span></span>
    <span><span class="chip b">Like</span><span class="chip b">Share</span><span class="chip">65k</span></span>
  </div>
  <div class="tips-body">
    <div class="tips-col">RESULT &nbsp;&nbsp;&nbsp; 100%<small>RIVERTON UNITED WIN</small></div>
    <div class="tips-col mid">SCORE &nbsp; 50% <span style="color:var(--blue);font-size:9px">▼</span><small>EASTMOOR VILLA 0<br>RIVERTON UNITED 2<br>RIVERTON</small></div>
    <div class="tips-col">1st GOAL &nbsp;&nbsp; 80%<small>ASHTON R</small></div>
  </div>
</div>

<div class="abs features">
  <div class="feat"><div class="ic"></div><div><h3>Predict</h3><p>Maecenas a sapien tortor quis tincidt lectus. Donec ullamcorper dui sit am lorem ultrices sed......»</p></div></div>
  <div class="feat"><div class="ic"></div><div><h3>Get Tips</h3><p>Maecenas a sapien tortor quis tincidt lectus. Donec ullamcorper dui sit am ultrices sed......»</p></div></div>
  <div class="feat"><div class="ic"></div><div><h3>Win</h3><p>Maecenas a sapien tortor quis tincidt lectus. Donec ullamcorper dui sit am ultrices sed......»</p></div></div>
</div>

<div class="abs section-title">TEMPOR INCIDIDUNT</div>

<div class="abs match" style="left:39px;top:582px"><div class="crest" style="left:36px"></div><div class="vs">V</div><div class="crest" style="left:133px"></div><div class="team" style="left:0">Northgate City</div><div class="team" style="left:113px">Glassford Palace</div><div class="date"><i></i>Sat 20 Dec 2014 12:45 PM</div><div class="predict">Predict Score Now!</div></div>
<div class="abs match" style="left:277px;top:582px"><div class="crest" style="left:36px"></div><div class="vs">V</div><div class="crest" style="left:133px"></div><div class="team" style="left:0">Northgate City</div><div class="team" style="left:113px">Glassford Palace</div><div class="date"><i></i>Sat 20 Dec 2014 12:45 PM</div><div class="predict">Predict Score Now!</div></div>
<div class="abs match" style="left:514px;top:582px"><div class="crest" style="left:36px"></div><div class="vs">V</div><div class="crest" style="left:133px"></div><div class="team" style="left:0">Northgate City</div><div class="team" style="left:113px">Glassford Palace</div><div class="date"><i></i>Sat 20 Dec 2014 12:45 PM</div><div class="predict">Predict Score Now!</div></div>
<div class="abs match" style="left:39px;top:797px"><div class="crest" style="left:36px"></div><div class="vs">V</div><div class="crest" style="left:133px"></div><div class="team" style="left:0">Northgate City</div><div class="team" style="left:113px">Glassford Palace</div><div class="date"><i></i>Sat 20 Dec 2014 12:45 PM</div><div class="predict">Predict Score Now!</div></div>
<div class="abs match" style="left:277px;top:797px"><div class="crest" style="left:36px"></div><div class="vs">V</div><div class="crest" style="left:133px"></div><div class="team" style="left:0">Northgate City</div><div class="team" style="left:113px">Glassford Palace</div><div class="date"><i></i>Sat 20 Dec 2014 12:45 PM</div><div class="predict">Predict Score Now!</div></div>
<div class="abs match" style="left:514px;top:797px"><div class="crest" style="left:36px"></div><div class="vs">V</div><div class="crest" style="left:133px"></div><div class="team" style="left:0">Northgate City</div><div class="team" style="left:113px">Glassford Palace</div><div class="date"><i></i>Sat 20 Dec 2014 12:45 PM</div><div class="predict">Predict Score Now!</div></div>

<div class="abs show-all">Show All &nbsp;➜</div>

<div class="abs footer"></div>
<div class="abs fh" style="left:39px">USEFUL LINKS</div>
<div class="abs flinks" style="left:40px">Home<br>About Us<br>Tables<br>Kitty<br>FAQ<br>Profile<br>History<br>Mini-Liga Admin<br>Contact</div>
<div class="abs fh" style="left:164px">HELP</div>
<div class="abs flinks" style="left:165px">Login<br>Register<br>Terms<br>Site Map<br>Privacy<br>Terms and Conditions</div>
<div class="abs feedback">✉ &nbsp; Send Us Feedback</div>
<svg class="abs social" style="left:299px" viewBox="0 0 24 24"><rect x="7" y="8" width="10" height="8" fill="#fff"/><path d="M7 8l5 4 5-4" stroke="#333" fill="none"/></svg>
<div class="abs social" style="left:330px"></div>
<div class="abs social" style="left:361px"></div>
<div class="abs social" style="left:393px"></div>
<div class="abs social" style="left:424px"></div>
<div class="abs social" style="left:455px"></div>
<div class="abs fh" style="left:559px">PUNDITS PREDICTIONS</div>
<div class="abs avatar" role="img" aria-label="Portrait photo of the pundit"></div>
<div class="abs quote">Sed ut perspiciatis unde omnis iste natus error sit voluptatem doloremque.....</div>
<div class="abs by">By Daniel Marsh</div>
<div class="abs copy">Copyright © PitchTally 2014. All Rights Reserved.</div>
</body>
</html>
```